Brambleton Pizza Website

We are working with Brambleton Pizza and designing them a website.

Some sites to use for content/competitors and inspiration:

https://fennimores.com
https://www.bhq-eats.com
https://brightorchard.com/en-us/

Thank you for taking the time to consider designing a website for us. We are web developers based in Stockton, CA, USA. Most of our projects go through the same process. Understanding this process may help you win a project with us. We custom-code all of our websites in-house. We don’t have any requirements as to what tools you use for your design, but we prefer Figma files. For any design that we label as four-stars, we send it to the client for review. The client picks the final design they want us to use. Once we complete this process, we will continue to show additional clients all the four-star sites and purchase them later. Your designs will have multiple chances to sell. For better chances of success, we ask that you follow these guidelines.

IMAGES:
If you use any images or icons in the design, we ask that you have a link to the asset so we can purchase the image/icon. Most of the designs we submit do not have the customer’s images on them unless they have some great images. Be creative; show us the feeling you are trying to portray with your image choices. Use any royalty-free site you choose. We subscribe to Quillstone and mainly use their images, but we can purchase images outside of Quillstone.

PLEASE NOTE: we will not submit designs to clients with watermarks on the images.

FONTS:
We ask that you identify the fonts used in the design. This can be done in a message if you want. We typically use Google Fonts and Quillstone Fonts.

CONTENT:
We're always open to different content and ideas. We often submit designs with stock images so the client can see our vision. We typically take pictures after the website launch to use their images with our vision. Lorem Ipsum is fine for paragraphs, but we ask that you write the headers in correct English. We want to be able to show the vision and identify the sections of the website.

INSPIRATION:
We typically add a couple of links in the brief of websites we like to help you get started in your design.

REVISIONS:
We do not often ask for revisions of the designs unless we see something in the design that may not appeal to the client. If there are slight changes that we want to make, we do that in the development process.

FEEDBACK:
We rarely give feedback on designs during the design process. We are working on many website projects and do not have the time to provide feedback. We usually respond if your request is well thought out and asks specific questions, but a note asking “feedback, please” usually goes unanswered.

```html
<!DOCTYPE html>
<html lang="en">
<head>
<meta charset="utf-8">
<title>Brambleton Pizza</title>
<link href="https://fonts.googleapis.com/css2?family=Poppins:wght@300;400;500;600;700;800&display=swap" rel="stylesheet">
<style>
:root{
  --red:#e3262a;
  --green:#2e9b2e;
  --ink:#1c1c1c;
  --text:#333333;
  --black:#0a0a0a;
  --blush:#f4eeee;
  --mist:#f4f4f4;
  --white:#ffffff;
}
*{box-sizing:border-box;margin:0;padding:0}
html,body{width:1200px;height:5063px;overflow:hidden;background:var(--white)}
body{font-family:'Poppins',sans-serif;color:var(--text);position:relative}
.abs{position:absolute}
section,header,footer{position:absolute;left:0;width:1200px;overflow:hidden}
.photo{position:absolute}

/* header */
.site-header{top:0;height:153px;background:var(--black)}
.brand{left:94px;top:40px;display:flex;align-items:center;gap:10px;color:var(--white);font-weight:700;font-size:20px;letter-spacing:1px}
.brand .dot{width:34px;height:34px;border-radius:50%;background:var(--red)}
.nav{left:0;top:100px;width:1200px;height:20px;font-size:13px;color:var(--white)}
.nav span{position:absolute;white-space:nowrap}
.nav .active::after{content:"";position:absolute;left:0;right:0;bottom:-6px;height:2px;background:var(--red)}
.search{left:856px;top:39px;width:173px;height:32px;border:2px solid var(--white);border-radius:16px;font-size:11px;color:#666;padding:6px 14px}

/* hero */
.hero{top:153px;height:515px;background:linear-gradient(90deg,#1e1e1e,#3a3a3a 60%,#262626)}
.hero h1{left:114px;top:92px;font-size:64px;font-weight:500;line-height:86px;color:var(--white)}
.hero p{left:114px;top:282px;width:600px;font-size:12px;line-height:16px;color:var(--white)}
.btn{position:absolute;display:flex;align-items:center;justify-content:center;border-radius:24px;font-size:16px;color:var(--white)}
.btn-red{background:var(--red)}
.btn-ghost{border:2px solid var(--red)}

/* about */
.about{top:668px;height:452px;background:var(--blush)}
.eyebrow{font-size:14px;color:var(--green);text-transform:uppercase;position:absolute}
.title{font-size:44px;font-weight:400;color:var(--ink);position:absolute}
.about p{left:703px;top:184px;width:430px;font-size:13px;line-height:22.5px;color:var(--text)}
.divider{position:absolute;width:80px;height:2px;background:var(--red)}

/* menus */
.menus{top:1120px;height:1001px;background:var(--white)}
.center{left:0;width:1200px;text-align:center}
.card-img{position:absolute;width:246px;height:246px;border-radius:6px}
.card-name{position:absolute;width:246px;text-align:center;font-size:24px;color:var(--ink)}

/* gallery */
.gallery{top:2121px;height:825px;background:var(--mist)}
.tile{position:absolute;width:232px;height:232px}
.pager{position:absolute;width:36px;height:36px;border-radius:5px;border:2px solid var(--red)}

/* stats */
.stats{top:2946px;height:379px;background:var(--white)}
.stat-box{position:absolute;width:133px;height:132px;border:2px solid var(--red);display:flex;align-items:center;justify-content:center}
.stat-num{position:absolute;width:200px;text-align:center;font-size:36px;font-weight:600;color:var(--red)}
.stat-label{position:absolute;width:240px;text-align:center;font-size:19px;color:var(--ink)}

/* offer */
.offer{top:3325px;height:436px;background:linear-gradient(90deg,#1a1412,#3a2c24 55%,#1e1714)}
.offer .lead{left:67px;top:32px;font-size:56px;font-weight:300;color:var(--white)}
.offer .big{left:65px;font-size:88px;font-weight:800;color:var(--white);line-height:92px}
.offer p{left:67px;top:303px;width:560px;font-size:12px;line-height:15px;color:var(--white)}

/* testimonials */
.testimonials{top:3761px;height:707px;background:var(--white)}
.red-band{left:212px;top:281px;width:782px;height:302px;background:var(--red)}
.frame{left:310px;top:202px;width:588px;height:440px;border:3px solid var(--ink);border-radius:6px}
.quote{position:absolute;width:46px;height:46px;border-radius:50%;background:var(--white);display:flex;align-items:center;justify-content:center;font-size:36px;font-weight:700;color:var(--ink);line-height:1}
.quote span{margin-top:14px}
.avatar{left:552px;top:236px;width:96px;height:96px;border-radius:50%;border:3px solid var(--white);background:linear-gradient(180deg,#9a9a9a,#4a4a4a 60%,#2a2a2a)}
.testimonials .msg{left:340px;top:366px;width:528px;text-align:center;font-size:14.5px;line-height:25px;color:var(--white)}
.testimonials .who{left:0;top:458px;width:1200px;text-align:center;font-size:22px;font-weight:500;color:var(--white)}
.stars{left:0;top:495px;width:1200px;text-align:center;font-size:20px;letter-spacing:4px;color:var(--white)}

/* newsletter */
.newsletter{top:4468px;height:285px;background:linear-gradient(90deg,#1b1512,#33261e 50%,#1b1512)}
.newsletter h2{top:38px;font-size:42px;font-weight:700;color:var(--white)}
.newsletter .sub{top:118px;font-size:20px;color:var(--white)}
.field{left:167px;top:189px;width:697px;height:51px;background:var(--white);font-size:16px;color:#777;padding:13px 22px}
.submit{left:876px;top:189px;width:173px;height:51px;background:var(--red);color:var(--white);font-size:16px;display:flex;align-items:center;justify-content:center}

/* footer */
.site-footer{top:4753px;height:310px;background:var(--black);color:var(--white)}
.contact{position:absolute;display:flex;gap:12px;font-size:16px;line-height:24px}
.ico{width:34px;height:34px;border-radius:50%;background:var(--white);display:flex;align-items:center;justify-content:center;flex:none}
.rule{left:67px;top:179px;width:1068px;height:1px;background:#555}
.foot-links{top:204px;left:0;width:1200px;font-size:13px}
.foot-links span{position:absolute;white-space:nowrap}
.sep{position:absolute;top:204px;width:1px;height:20px;background:#888}
.copy{left:67px;top:266px;font-size:14px}
.social{position:absolute;top:258px;width:36px;height:36px;border-radius:50%;background:var(--red)}
</style>
</head>
<body>

<header class="site-header">
  <div class="brand abs"><span class="dot"></span>BRAMBLETON PIZZA</div>
  <nav class="nav abs">
    <span class="active" style="left:453px">Home</span>
    <span style="left:526px">Our Menus</span>
    <span style="left:645px">About Us</span>
    <span style="left:742px">Order Online</span>
    <span style="left:862px">Gallery</span>
    <span style="left:957px">Reviews</span>
    <span style="left:1054px">Contact Us</span>
  </nav>
  <div class="search abs">Search
    <svg class="abs" style="right:12px;top:6px" width="16" height="16" viewBox="0 0 16 16"><circle cx="7" cy="7" r="5" fill="none" stroke="#fff" stroke-width="2"/><line x1="11" y1="11" x2="15" y2="15" stroke="#fff" stroke-width="2"/></svg>
  </div>
  <svg class="abs" style="left:1052px;top:38px" width="30" height="30" viewBox="0 0 30 30"><path d="M2 6h5l4 14h13l3-10H9" fill="none" stroke="#fff" stroke-width="2"/><circle cx="13" cy="25" r="2" fill="#fff"/><circle cx="22" cy="25" r="2" fill="#fff"/><circle cx="25" cy="5" r="4" fill="#e3262a"/></svg>
  <svg class="abs" style="left:1100px;top:38px" width="30" height="30" viewBox="0 0 30 30"><circle cx="15" cy="10" r="6" fill="none" stroke="#fff" stroke-width="2"/><path d="M4 28c1-7 6-10 11-10s10 3 11 10z" fill="none" stroke="#fff" stroke-width="2"/></svg>
</header>

<section class="hero">
  <div class="photo" role="img" aria-label="Whole pizza with a slice cut out, on a dark stone surface" style="left:822px;top:0;width:420px;height:515px;border-radius:50% 0 0 50%;background:radial-gradient(circle at 55% 50%,#e0a050,#c0692a 50%,#7a3a18 75%,#3a2a22)"></div>
  <h1 class="abs">A Slice Of Heaven<br>In Every Bite pizza</h1>
  <p class="abs">Lorem ipsum dolor sit amet, consectetur adipiscing elit, sed do eiusmod tempor incididunt ut labore et dolore magna aliqua.</p>
  <div class="btn btn-red" style="left:116px;top:347px;width:222px;height:48px">Book A Table</div>
  <div class="btn btn-ghost" style="left:357px;top:347px;width:222px;height:48px">View Menu</div>
</section>

<section class="about">
  <div class="photo" role="img" aria-label="Slice of pizza lifted from a whole pizza with tomatoes and olives" style="left:0;top:0;width:642px;height:452px;background:radial-gradient(ellipse at 40% 60%,#d89a4a,#b0561f 45%,#5a2e18 75%,#2a1e18)"></div>
  <div class="eyebrow" style="left:703px;top:74px">Who We Are</div>
  <h2 class="title" style="left:703px;top:88px">About Us</h2>
  <div class="divider" style="left:703px;top:146px;width:54px"></div>
  <p class="abs">Sed ut perspiciatis unde omnis iste natus error sit voluptatem accusantium doloremque laudantium, totam rem aperiam, eaque ipsa quae ab illo inventore veritatis et quasi architecto beatae vitae dicta sunt explicabo. Nemo enim ipsam voluptatem quia voluptas sit aspernatur aut odit aut fugit, sed quia consequuntur magni dolores eos qui ratione voluptatem sequi nesciunt.</p>
  <div class="btn btn-red" style="left:703px;top:349px;width:124px;height:34px;font-size:13px">Read More</div>
</section>

<section class="menus">
  <div class="eyebrow center" style="top:68px">Order Online Now</div>
  <h2 class="title center" style="top:82px">Our Menus</h2>
  <div class="divider" style="left:560px;top:143px"></div>

  <div class="card-img" role="img" aria-label="Italian pizza on a wooden board" style="left:157px;top:200px;background:radial-gradient(circle,#d98b3d,#a24a1c 62%,#4a2a18)"></div>
  <div class="card-img" role="img" aria-label="Roman pizza on a dark table" style="left:477px;top:200px;background:radial-gradient(circle,#e89a52,#b4602a 50%,#2b2b2b 72%)"></div>
  <div class="card-img" role="img" aria-label="Vegetable pizza with peppers" style="left:797px;top:200px;background:radial-gradient(circle,#e0a24f,#b06a2c 58%,#3a3a3a 76%)"></div>
  <div class="card-name" style="left:157px;top:466px">Italian Pizza</div>
  <div class="card-name" style="left:477px;top:466px">Roman pizza</div>
  <div class="card-name" style="left:797px;top:466px">Veg pizza</div>

  <div class="card-img" role="img" aria-label="Cheese pizza slice with stretching cheese" style="left:157px;top:542px;background:linear-gradient(160deg,#e7c98a,#c9552a 60%,#6a2a18)"></div>
  <div class="card-img" role="img" aria-label="BBQ chicken pizza" style="left:477px;top:542px;background:radial-gradient(circle,#e7a25a,#c0682e 58%,#c9c9d6 76%)"></div>
  <div class="card-img" role="img" aria-label="Stuffed crust pizza with dips" style="left:797px;top:542px;background:radial-gradient(circle,#d9a04e,#8a5a2c 58%,#2f2f2f 78%)"></div>
  <div class="card-name" style="left:157px;top:808px">Cheese Pizza</div>
  <div class="card-name" style="left:477px;top:808px">BBQ Chicken Pizza</div>
  <div class="card-name" style="left:797px;top:808px">Stuffed crust</div>

  <div class="btn btn-red" style="left:520px;top:891px;width:160px;height:41px;font-size:17px">View More</div>
</section>

<section class="gallery">
  <div class="eyebrow center" style="top:68px">Our Gallery</div>
  <h2 class="title center" style="top:82px">Portfolio</h2>
  <div class="divider" style="left:560px;top:143px"></div>

  <div class="tile" role="img" aria-label="Pizza with tomatoes and limes" style="left:90px;top:202px;background:radial-gradient(circle,#e09a4a,#b45a22 58%,#3a2a1a 80%)"></div>
  <div class="tile" role="img" aria-label="Pizza on a dark board" style="left:353px;top:202px;background:radial-gradient(circle,#e8964c,#b4582a 50%,#2a2a2a 72%)"></div>
  <div class="tile" role="img" aria-label="Pizza with olives and peppers" style="left:615px;top:202px;background:radial-gradient(circle,#e2a54f,#b46a2a 62%,#222 82%)"></div>
  <div class="tile" role="img" aria-label="Cheese stretching from a slice" style="left:876px;top:202px;background:linear-gradient(160deg,#2a2a2a,#e8d9a8 50%,#6a4a2a)"></div>
  <div class="tile" role="img" aria-label="Pepperoni pizza" style="left:90px;top:466px;background:linear-gradient(180deg,#c24a18,#e8a040 55%,#7a2a10)"></div>
  <div class="tile" role="img" aria-label="Mushroom pizza with greens" style="left:353px;top:466px;background:radial-gradient(circle,#8a7a3a,#c08a4a 55%,#a8202a)"></div>
  <div class="tile" role="img" aria-label="Jalapeno pizza" style="left:615px;top:466px;background:radial-gradient(circle,#a8a24a,#c8a05a 60%,#7a7a6a)"></div>
  <div class="tile" role="img" aria-label="Spinach and corn pizza" style="left:876px;top:466px;background:linear-gradient(160deg,#4a3a2a,#c89a3a 45%,#3a5a2a)"></div>

  <div class="pager" style="left:558px;top:749px;background:#f2b8b9;border-color:#f2b8b9"><svg width="32" height="32" viewBox="0 0 32 32"><path d="M19 9l-7 7 7 7" fill="none" stroke="#fff" stroke-width="2.5"/></svg></div>
  <div class="pager" style="left:605px;top:749px"><svg width="32" height="32" viewBox="0 0 32 32"><path d="M13 9l7 7-7 7" fill="none" stroke="#e3262a" stroke-width="2.5"/></svg></div>
</section>

<section class="stats">
  <div class="stat-box" style="left:169px;top:88px"><svg width="80" height="80" viewBox="0 0 80 80"><path d="M28 72s-16-18-16-30a16 16 0 0132 0c0 12-16 30-16 30z" fill="#2e9b2e"/><circle cx="28" cy="42" r="6" fill="#fff"/><path d="M58 40s-9-10-9-17a9 9 0 0118 0c0 7-9 17-9 17z" fill="#2e9b2e"/><circle cx="58" cy="23" r="3.5" fill="#fff"/><path d="M36 72c10 0 24-8 22-28" fill="none" stroke="#2e9b2e" stroke-width="2" stroke-dasharray="4 4"/></svg></div>
  <div class="stat-box" style="left:416px;top:88px"><svg width="80" height="80" viewBox="0 0 80 80"><path d="M20 22c-10 14-8 32 8 42M60 22c10 14 8 32-8 42" fill="none" stroke="#2e9b2e" stroke-width="5" stroke-dasharray="6 3"/><polygon points="40,22 46,36 61,37 49,46 53,61 40,53 27,61 31,46 19,37 34,36" fill="#2e9b2e"/></svg></div>
  <div class="stat-box" style="left:666px;top:88px"><svg width="80" height="80" viewBox="0 0 80 80"><polygon points="38,6 41,13 48,13 42,18 44,25 38,21 32,25 34,18 28,13 35,13" fill="#2e9b2e"/><polygon points="20,14 22,18 26,18 23,21 24,25 20,23 16,25 17,21 14,18 18,18" fill="#2e9b2e"/><polygon points="56,14 58,18 62,18 59,21 60,25 56,23 52,25 53,21 50,18 54,18" fill="#2e9b2e"/><circle cx="38" cy="38" r="9" fill="#2e9b2e"/><path d="M18 70c0-14 9-20 20-20s20 6 20 20z" fill="#2e9b2e"/><circle cx="58" cy="62" r="10" fill="#2e9b2e" stroke="#fff" stroke-width="2"/><path d="M53 62l4 4 7-7" fill="none" stroke="#fff" stroke-width="2.5"/></svg></div>
  <div class="stat-box" style="left:913px;top:88px"><svg width="80" height="80" viewBox="0 0 80 80" fill="#2e9b2e"><circle cx="22" cy="26" r="7"/><circle cx="58" cy="26" r="7"/><circle cx="40" cy="20" r="8"/><path d="M8 54c0-10 6-16 14-16s14 6 14 16z"/><path d="M44 54c0-10 6-16 14-16s14 6 14 16z"/><circle cx="30" cy="44" r="8"/><circle cx="50" cy="44" r="8"/><path d="M14 72c0-10 7-16 16-16s16 6 16 16z"/><path d="M34 72c0-10 7-16 16-16s16 6 16 16z"/></svg></div>

  <div class="stat-num" style="left:136px;top:231px">50</div>
  <div class="stat-num" style="left:383px;top:231px">30</div>
  <div class="stat-num" style="left:632px;top:231px">100</div>
  <div class="stat-num" style="left:879px;top:231px">30</div>
  <div class="stat-label" style="left:116px;top:282px">Pizza Branches</div>
  <div class="stat-label" style="left:363px;top:282px">Number of Awards</div>
  <div class="stat-label" style="left:612px;top:282px">Happy Customer</div>
  <div class="stat-label" style="left:859px;top:282px">Staff</div>
</section>

<section class="offer">
  <div class="photo" role="img" aria-label="Whole pizza with olives, peppers and corn" style="left:778px;top:30px;width:377px;height:377px;border-radius:50%;background:radial-gradient(circle,#e8b04a,#d08a30 55%,#a4581e 85%,#6a3a1a)"></div>
  <div class="lead abs">Amazing Offers Online</div>
  <div class="big abs" style="top:100px">50% OFF PIZZAS</div>
  <div class="big abs" style="top:193px">ONLINE</div>
  <p class="abs">Lorem ipsum dolor sit amet, consectetur adipiscing elit, sed do eiusmod tempor incididunt ut labore et dolore magna aliqua.</p>
  <div class="btn btn-red" style="left:67px;top:357px;width:143px;height:40px;font-size:15px">Order Now</div>
</section>

<section class="testimonials">
  <div class="eyebrow center" style="top:68px">Our Reviews</div>
  <h2 class="title center" style="top:82px">Testimonials</h2>
  <div class="divider" style="left:555px;top:143px"></div>

  <div class="red-band abs"></div>
  <div class="frame abs"></div>
  <div class="quote" style="left:384px;top:185px"><span>&ldquo;</span></div>
  <div class="quote" style="left:760px;top:618px"><span>&rdquo;</span></div>
  <div class="photo avatar" role="img" aria-label="Customer portrait"></div>
  <p class="msg abs">There are many variations of passages of Lorem Ipsum available, but the majority have suffered alteration in some form, by injected humour, or randomised words which don't look even slightly</p>
  <div class="who abs">OWEN MARSH</div>
  <div class="stars abs">★★★★★</div>

  <svg class="abs" style="left:130px;top:400px" width="24" height="24" viewBox="0 0 24 24"><path d="M15 5l-7 7 7 7" fill="none" stroke="#e3262a" stroke-width="2"/></svg>
  <svg class="abs" style="left:1044px;top:400px" width="24" height="24" viewBox="0 0 24 24"><path d="M9 5l7 7-7 7" fill="none" stroke="#e3262a" stroke-width="2"/></svg>
</section>

<section class="newsletter">
  <h2 class="abs center">SUBSCRIBE TO OUR NEWSLETTER</h2>
  <div class="sub abs center">Be the first to know about new products and exclusive offers.</div>
  <div class="field abs">Enter a valid email address</div>
  <div class="submit abs">SUBMIT</div>
</section>

<footer class="site-footer">
  <div class="contact" style="left:170px;top:66px">
    <span class="ico"><svg width="18" height="18" viewBox="0 0 18 18"><path d="M9 17s-6-6-6-10a6 6 0 0112 0c0 4-6 10-6 10z" fill="#000"/><circle cx="9" cy="7" r="2" fill="#fff"/></svg></span>
    <span>ADDRESS:<br>Lorem ipsum dolor sit<br>amet, consectetur</span>
  </div>
  <div class="contact" style="left:508px;top:66px">
    <span class="ico"><svg width="18" height="18" viewBox="0 0 18 18"><path d="M4 2l3 0 1 4-2 1c1 2 3 4 5 5l1-2 4 1v3c0 1-1 2-2 2C8 16 2 10 2 4c0-1 1-2 2-2z" fill="#000"/></svg></span>
    <span>PHONE:<br>+1 888 888 8888</span>
  </div>
  <div class="contact" style="left:803px;top:66px">
    <span class="ico"><svg width="18" height="18" viewBox="0 0 18 18"><rect x="2" y="4" width="14" height="10" fill="#000"/><path d="M2 4l7 6 7-6" fill="none" stroke="#fff" stroke-width="1.5"/></svg></span>
    <span>EMAIL:<br>info@brambletonpizza.com</span>
  </div>

  <div class="rule abs"></div>
  <div class="foot-links abs">
    <span style="left:297px">Our Menus</span>
    <span style="left:418px">About Us</span>
    <span style="left:513px">Order Online</span>
    <span style="left:633px">Gallery</span>
    <span style="left:729px">Reviews</span>
    <span style="left:825px">Contact Us</span>
  </div>
  <div class="sep" style="left:397px"></div>
  <div class="sep" style="left:497px"></div>
  <div class="sep" style="left:618px"></div>
  <div class="sep" style="left:703px"></div>
  <div class="sep" style="left:802px"></div>

  <div class="copy abs">Copyright © 2025, Company Name. All Rights Reserved.</div>
  <span class="social" style="left:1003px"></span>
  <span class="social" style="left:1050px"></span>
  <span class="social" style="left:1097px"></span>
</footer>

</body>
</html>
```